Executive Coaching and Spiritual Development Company needs a business card design.

We need a business card design for our company. We already have a logo that was created through Brightloom that we will submit and would like to see this work on black, blue and white backgrounds. Our personal information should be included as well. The design should communicate trust, spirituality, support and partnership.

Industry/Entity Type

Business

Colors
0255a3
33a6d7
ffffff
000000
474747

Requirements
Nice to have
• The colors offered here are just ideas--we are open to other suggestions, too.

```html
<!DOCTYPE html>
<html lang="en">
<head>
<meta charset="utf-8">
<title>Innerway business card</title>
<link rel="stylesheet" href="https://fonts.googleapis.com/css2?family=Arvo:wght@700&family=Lato:wght@400;700;900&display=swap">
<style>
  :root {
    --backdrop: #2b2c2e;
    --card: #f7f7f7;
    --card-shade: #ebebeb;
    --ink: #0e2233;
    --blue: #0255a3;
    --grey: #474747;
    --soft-grey: #c9c9c9;
    --faint: #dcdcdc;
  }
  * { margin: 0; padding: 0; box-sizing: border-box; }
  html, body {
    width: 1200px; height: 746px; overflow: hidden;
    background: var(--backdrop);
  }
  .canvas {
    position: relative; width: 1200px; height: 746px;
    display: flex; align-items: center; justify-content: center; gap: 40px;
  }
  .card {
    position: relative; width: 540px; height: 310px; overflow: hidden;
    background: linear-gradient(160deg, #ffffff 0%, var(--card) 55%, var(--card-shade) 100%);
    box-shadow: 0 14px 30px rgba(0,0,0,.55);
  }
  .card-band { position: absolute; left: 0; bottom: 0; width: 540px; height: 310px; }

  .brand {
    position: absolute; display: flex; align-items: center; gap: 16px;
  }
  .brand-mark {
    border: 4px solid var(--ink); border-radius: 50%;
  }
  .brand-name {
    font-family: "Arvo", Georgia, serif; font-weight: 700; color: var(--ink);
    letter-spacing: .5px; line-height: 1;
  }
  .card--back .brand { left: 60px; top: 105px; }
  .card--back .brand-mark { width: 92px; height: 92px; }
  .card--back .brand-name { font-size: 58px; }

  .card--front .brand { left: 56px; top: 44px; }
  .card--front .brand-mark { width: 74px; height: 74px; }
  .card--front .brand-name { font-size: 46px; }

  .faint-ring {
    position: absolute; border: 3px solid var(--faint); border-radius: 50%;
  }
  .card--back .faint-ring { width: 70px; height: 70px; right: 34px; top: 44px; }
  .card--front .faint-ring { width: 92px; height: 92px; right: 44px; top: 150px; }

  .person {
    position: absolute; right: 40px; top: 120px; text-align: right;
    font-family: "Lato", Arial, sans-serif; line-height: 1;
  }
  .person-name { color: var(--blue); font-weight: 900; font-size: 19px; letter-spacing: .3px; }
  .person-role { color: #9a9a9a; font-weight: 400; font-size: 15px; letter-spacing: .5px; margin-top: 2px; margin-right: 18px; }

  .icon-tab {
    position: absolute; left: 16px; top: 192px; width: 40px; height: 108px;
    background: var(--blue); border-radius: 0 0 8px 0;
    display: flex; flex-direction: column; align-items: center; justify-content: space-around;
    padding: 6px 0;
  }
  .contact {
    position: absolute; left: 74px; top: 200px; list-style: none;
    font-family: "Lato", Arial, sans-serif; font-weight: 900; font-size: 16px; color: #111;
  }
  .contact li { height: 32px; line-height: 32px; }
</style>
</head>
<body>
<main class="canvas">

  <section class="card card--back" aria-label="Card back">
    <svg class="card-band" viewBox="0 0 540 310" aria-hidden="true">
      <path d="M0 310 L0 290 L360 290 Q380 290 392 268 L540 268 L540 310 Z" fill="#d9d9d9"/>
      <path d="M392 268 Q404 246 430 240 L540 212 L540 226 L446 252 Q420 258 410 268 Z" fill="var(--blue)"/>
    </svg>
    <div class="faint-ring"></div>
    <div class="brand">
      <span class="brand-mark"></span>
      <span class="brand-name">Innerway</span>
    </div>
  </section>

  <section class="card card--front" aria-label="Card front">
    <svg class="card-band" viewBox="0 0 540 310" aria-hidden="true">
      <path d="M0 310 L0 300 L380 300 Q392 300 398 288 L540 288 L540 310 Z" fill="#d9d9d9"/>
      <path d="M398 288 Q410 268 436 262 L540 240 L540 254 L452 274 Q424 280 416 288 Z" fill="var(--blue)"/>
    </svg>
    <div class="brand">
      <span class="brand-mark"></span>
      <span class="brand-name">Innerway</span>
    </div>
    <div class="person">
      <div class="person-name">YOUR NAME</div>
      <div class="person-role">DIRECTOR</div>
    </div>
    <div class="faint-ring"></div>

    <div class="icon-tab">
      <svg width="16" height="22" viewBox="0 0 16 22" aria-label="Phone" role="img">
        <rect x="1.5" y="1.5" width="13" height="19" rx="2" fill="none" stroke="#fff" stroke-width="1.8"/>
        <line x1="4" y1="17" x2="12" y2="17" stroke="#fff" stroke-width="1.5"/>
      </svg>
      <svg width="22" height="16" viewBox="0 0 22 16" aria-label="Email" role="img">
        <rect x="1" y="1" width="20" height="14" fill="#fff"/>
        <path d="M1 1 L11 9 L21 1" fill="none" stroke="var(--blue)" stroke-width="1.6"/>
      </svg>
      <svg width="22" height="22" viewBox="0 0 22 22" aria-label="Website" role="img">
        <circle cx="11" cy="11" r="9" fill="none" stroke="#fff" stroke-width="2"/>
        <circle cx="11" cy="11" r="5" fill="#fff"/>
      </svg>
    </div>
    <ul class="contact">
      <li>514-555-0147</li>
      <li>hello@innerway.ca</li>
      <li>www.innerway.ca</li>
    </ul>
  </section>

</main>
</body>
</html>
```